Commercial, Public Works, Contractor needs a modern web design

We are a General and Engineering contracting firm with vast experience in our industry. Our focus is on Commercial, Tenant Improvement, Restaurants, and Public Works. We are opening a new business and would like that excitement and energy to show through the new web design. The colors we like are black, red and grey, we are open to color ideas. Attached is our logo design.

Industry/Entity Type

Restaurant

```html
<!DOCTYPE html>
<html lang="en">
<head>
<meta charset="utf-8">
<title>Kestrel Build, Inc. — Engineering Contracting</title>
<link href="https://fonts.googleapis.com/css2?family=Montserrat:wght@400;500;600&family=Mulish:wght@400;600&display=swap" rel="stylesheet">
<style>
:root{
  --red:#c4101e;
  --red-dark:#9c0d17;
  --red-deep:#8a0a12;
  --ink:#1c1c1c;
  --text:#444;
  --muted:#5a5a5a;
  --line:#e2e2e2;
  --hero-bg:#f3f3f3;
  --footer:#2f2f2f;
  --social:#1f5fa8;
  --btn:#1e1e1e;
}
*{box-sizing:border-box;margin:0;padding:0}
html,body{width:1106px;height:1200px;overflow:hidden;background:#fff}
body{position:relative;font-family:"Mulish",sans-serif;color:var(--text)}
.brand{position:absolute;left:138px;top:34px;font-family:"Montserrat",sans-serif;font-weight:600;font-size:20px;color:var(--red);display:flex;align-items:center;gap:8px}
.brand-mark{width:22px;height:22px;border-radius:50%;background:var(--red)}
.social{position:absolute;left:898px;top:63px;display:flex;gap:4px}
.social span{width:20px;height:20px;border-radius:3px;background:var(--social)}
.nav{position:absolute;left:0;top:98px;width:1106px;height:39px;background:linear-gradient(#d41523,#b30d19);display:flex;padding-left:135px}
.nav a{font-family:"Montserrat",sans-serif;font-weight:500;font-size:13px;color:#fff;text-decoration:none;line-height:39px;padding:0 22px;border-right:1px solid rgba(0,0,0,.18)}
.nav a.active{background:var(--red-deep);padding:0 23px}
.nav a:last-child{border-right:none}
.hero{position:absolute;left:0;top:137px;width:1106px;height:403px;background:var(--hero-bg);overflow:hidden}
.hero-photo{position:absolute;left:340px;top:0;width:766px;height:403px;background:linear-gradient(90deg,var(--hero-bg) 0%,#c9d6e3 20%,#9fb9d4 50%,#b8c98a 80%,#a9c94a 100%)}
.hero-copy{position:absolute;left:136px;top:124px}
.hero-kicker{font-family:"Montserrat",sans-serif;font-size:25px;color:#1a1a1a;line-height:1.1}
.hero-title{font-family:"Montserrat",sans-serif;font-weight:400;font-size:35px;color:#111;line-height:1.3;margin-bottom:8px}
.hero-text{font-size:10px;line-height:16px;color:#555;width:320px}
.dots{display:flex;gap:3px;margin-top:14px}
.dots span{width:12px;height:12px;border-radius:50%;background:#b9b9b9}
.dots span:first-child{background:#555}
.services{position:absolute;left:134px;top:556px;width:837px;height:231px;border:1px solid var(--line);display:flex;background:#fff;box-shadow:0 8px 30px rgba(0,0,0,.05)}
.service{flex:1;border-right:1px solid var(--line);text-align:center;padding-top:22px}
.service:last-child{border-right:none}
.service-icon{width:82px;height:82px;border-radius:50%;border:1px solid #ddd;margin:0 auto;display:flex;align-items:center;justify-content:center}
.service h3{font-family:"Montserrat",sans-serif;font-weight:500;font-size:17px;color:var(--ink);margin:14px 0 8px}
.service p{font-size:10px;line-height:16px;color:var(--muted);padding:0 16px}
.btn{display:inline-block;font-family:"Montserrat",sans-serif;font-size:11px;color:#fff;text-decoration:none;width:91px;height:26px;line-height:26px;text-align:center}
.btn-dark{background:var(--btn);margin-top:12px}
.btn-red{background:var(--red);margin-top:10px}
.about{position:absolute;left:134px;top:848px;width:360px}
.about h2{font-family:"Montserrat",sans-serif;font-weight:400;font-size:23px;color:#111;margin-bottom:8px}
.about p{font-size:10px;line-height:16px;color:var(--text);margin-bottom:7px}
.feature{position:absolute;top:848px;width:217px}
.feature-img{height:97px}
.feature h3{font-family:"Montserrat",sans-serif;font-weight:400;font-size:18px;color:var(--red);margin:8px 0 4px 1px}
.feature p{font-size:10px;line-height:16px;color:var(--text);padding-left:2px}
.footer{position:absolute;left:0;top:1105px;width:1106px;height:95px;background:var(--footer)}
.footer-nav{position:absolute;left:135px;top:24px;font-family:"Montserrat",sans-serif;font-size:12px;color:#fff}
.footer-nav a{color:#fff;text-decoration:none}
.footer-nav span{margin:0 7px}
.copy{position:absolute;left:135px;top:50px;font-size:10px;color:#ddd}
</style>
</head>
<body>
<div class="brand"><span class="brand-mark"></span>Kestrel Build, Inc.</div>
<div class="social"><span></span><span></span><span></span></div>

<nav class="nav">
  <a class="active" href="#">HOME</a><a href="#">ABOUT US</a><a href="#">SERVICES</a><a href="#">ENGINEERING</a><a href="#">MISSION</a><a href="#">SUPPORT</a><a href="#">CONTACT</a>
</nav>

<section class="hero">
  <div class="hero-photo" role="img" aria-label="Three engineers in hard hats and safety vests reviewing plans at a crane-filled construction site"></div>
  <div class="hero-copy">
    <p class="hero-kicker">Mauris vel lacus vitae felis</p>
    <h1 class="hero-title">Engineering Contracting</h1>
    <p class="hero-text">Curabitur iaculis tempus eros Curabitur vel mi sit amet magna malesuada ultrices Ut nisi erat fermentum vel congue id euismod in elit Fusce ultricies orci ac feugiat suscipit leo massa sod</p>
    <div class="dots"><span></span><span></span><span></span><span></span></div>
  </div>
</section>

<section class="services">
  <div class="service">
    <div class="service-icon"><svg width="46" height="48" viewBox="0 0 46 48" fill="#b5101b"><rect x="14" y="2" width="18" height="40"/><rect x="2" y="14" width="12" height="28"/><rect x="32" y="10" width="12" height="32"/><rect x="0" y="42" width="46" height="4"/><g fill="#fff"><rect x="18" y="8" width="3" height="30"/><rect x="25" y="8" width="3" height="30"/><rect x="6" y="18" width="3" height="22"/><rect x="36" y="14" width="3" height="26"/></g></svg></div>
    <h3>Commercial</h3>
    <p>Etiam est nunc venenatis in tristique eu imperdiet ac nisl Cum sociis</p>
    <a class="btn btn-dark" href="#">Read More</a>
  </div>
  <div class="service">
    <div class="service-icon"><svg width="58" height="34" viewBox="0 0 58 34" fill="none" stroke="#b5101b" stroke-width="3"><rect x="12" y="2" width="32" height="10"/><rect x="2" y="12" width="26" height="10"/><rect x="28" y="12" width="28" height="10"/><rect x="10" y="22" width="22" height="10"/><rect x="32" y="22" width="18" height="10"/></svg></div>
    <h3>Tenant Improvement</h3>
    <p>Etiam est nunc venenatis in tristique eu imperdiet ac nisl Cum sociis</p>
    <a class="btn btn-dark" href="#">Read More</a>
  </div>
  <div class="service">
    <div class="service-icon"><svg width="50" height="46" viewBox="0 0 50 46" fill="#b5101b"><rect x="3" y="0" width="44" height="6"/><path d="M0 8h50l-3 10H3z"/><rect x="6" y="20" width="38" height="26"/><rect x="14" y="26" width="22" height="10" fill="#fff"/></svg></div>
    <h3>Restaurants</h3>
    <p>Etiam est nunc venenatis in tristique eu imperdiet ac nisl Cum sociis</p>
    <a class="btn btn-dark" href="#">Read More</a>
  </div>
  <div class="service">
    <div class="service-icon"><svg width="48" height="36" viewBox="0 0 48 36" fill="#b5101b"><circle cx="10" cy="8" r="6"/><circle cx="38" cy="8" r="6"/><circle cx="24" cy="11" r="8"/><rect x="0" y="16" width="16" height="12" rx="5"/><rect x="32" y="16" width="16" height="12" rx="5"/><rect x="12" y="20" width="24" height="16" rx="6"/></svg></div>
    <h3>Public Works</h3>
    <p>Etiam est nunc venenatis in tristique eu imperdiet ac nisl Cum sociis</p>
    <a class="btn btn-dark" href="#">Read More</a>
  </div>
</section>

<section class="about">
  <h2>ABOUT OUR COMPANY</h2>
  <p>Morbi ornare gravida elit Integer congue augue et malesuada iaculis ipsum dui aliquet felis at cursus magna nisl nec elit Praesent elementum elit at tellus nec ultricies sit amet porttitor mattis enim In massa libero interdum nec interdum vel blandit sed nulla In ullamcorper est eget tempor cursus neque</p>
  <p>Curabitur iaculis tempus eros Curabitur vel mi sit amet magna malesuada ultrices Ut nisi erat fermentum vel congue id euismod in elit Fusce ultricies orci ac feugiat suscipit leo massa sodales velit et scelerisque mi tortor at ipsum</p>
  <a class="btn btn-red" href="#">Read More</a>
</section>

<article class="feature" style="left:518px">
  <div class="feature-img" role="img" aria-label="Engineers in hard hats reviewing a laptop at an industrial plant" style="background:linear-gradient(90deg,#cfd3d8,#e9ecef 45%,#c85a3a 70%,#3c3f46)"></div>
  <h3>Recent Project</h3>
  <p>Morbi ornare gravida elit Integer congue augue et malesuada iaculis ipsum dui aliquet felis at cursus magna nisl nec elit Praesent</p>
</article>
<article class="feature" style="left:754px">
  <div class="feature-img" role="img" aria-label="Engineer in a hard hat and orange vest studying plans" style="background:linear-gradient(90deg,#c9cdd3,#eef0f2 45%,#e7d4bf 70%,#e07a2a)"></div>
  <h3>How we Work</h3>
  <p>Morbi ornare gravida elit Integer congue augue et malesuada iaculis ipsum dui aliquet felis at cursus magna nisl nec elit Praesent</p>
</article>

<footer class="footer">
  <div class="footer-nav"><a href="#">Home</a><span>|</span><a href="#">About Us</a><span>|</span><a href="#">Services</a><span>|</span><a href="#">Engineering</a><span>|</span><a href="#">Support</a><span>|</span><a href="#">Contact</a></div>
  <p class="copy">© 2015 Company Name &nbsp;All right reserved &nbsp;Term of Use</p>
</footer>
</body>
</html>
```